Business Card: RW Office Partners - Your organised problem solver

Business Name: RW Office Partners
Website: www.rwofficepartners.com.au
Email: marisol@rwofficepartners.com.au
Mobile: 61 482 907 236
Facebook: @rwofficepartners
Instrgram: @rwofficepartners

Brading Colours:
HEX
#986474
#ddccd3
#7a8498
#c9d8e4
#000000
#ffffff

Tag Line: Your organised problem solver

Link to DRAFT website:
https://deskhelpcollective.wixsite.com/rw-office-partners

About Page from the website:
My name is Marisol Wrenfield, and I would love to assist you to become more productive in your day to day and achieve your business and personal goals.
My mission is to give you time, time to work on the important tasks of your business or to be able to spend more time with your family. I will take on the tasks you don’t have time for, don’t know well or simply don’t like to do.
I have an extensive background in Administration, Tender Coordination, Document Control, WHS and Quality Management working primarily in the Construction, Mining and Corporate World.
I am passionate about being organised, having order and making things in your life (and mine) easier! I love to watch something unfold and grow into something amazing! I am known for being the go-to problem solver, the organiser of all things, producing high standards of work even under pressure. I’m also a confident communicator, and I understand that you’re busy running your business.

Target Market(s)

Small to Medium Business who require assistance in their business by a virtual assistant.

Industry/Entity Type

Virtual Assistant

Contact Information for Business Card

Mobile: 61 482 907 236

Font styles to use
Sans Serif

Colors
ffffff

Requirements
Must have
• Branding Colours as outlined.
Contact Details as outlined.
Logo as provided.
Proper contact details - mobile, facebook, instragm, website.
Simple, Elegant, very clean looking.
Should not have
• Note cute with pictures.
Not too girly as still want to market to construction companies.

```html
<!DOCTYPE html>
<html lang="en">
<head>
<meta charset="utf-8">
<title>RW Office Partners – Business Card</title>
<link href="https://fonts.googleapis.com/css2?family=Roboto:wght@400;500;700&family=Patrick+Hand&display=swap" rel="stylesheet">
<style>
  :root {
    --mauve: #8b6070;
    --mauve-light: #ddccd3;
    --slate: #7a8498;
    --ice: #c9d8e4;
    --ink: #3a3a3a;
    --white: #ffffff;
    --stage: #6b6868;
  }
  * { box-sizing: border-box; margin: 0; padding: 0; }
  html, body { width: 1200px; height: 1200px; overflow: hidden; }
  body {
    background: var(--stage);
    font-family: "Roboto", Arial, sans-serif;
    position: relative;
  }
  .card {
    position: absolute;
    width: 712px;
    height: 418px;
    border-radius: 22px;
    overflow: hidden;
  }
  .card-front {
    left: 238px; top: 118px;
    background: var(--mauve);
    display: flex; align-items: center; justify-content: center;
  }
  .front-brand {
    color: var(--white);
    font-weight: 500;
    font-size: 54px;
    letter-spacing: 0.5px;
  }
  .card-back {
    left: 231px; top: 645px;
    background: var(--white);
  }
  .back-wave { position: absolute; inset: 0; }
  .back-brand {
    position: absolute; left: 40px; top: 58px;
    color: var(--mauve);
    font-weight: 500;
    font-size: 40px;
    letter-spacing: 0.3px;
  }
  .tagline {
    position: absolute; left: 40px; top: 136px;
    font-family: "Patrick Hand", cursive;
    font-size: 23px;
    color: var(--ink);
  }
  .holder {
    position: absolute; right: 32px; top: 174px;
    text-align: right; color: var(--white);
  }
  .holder-name { font-weight: 700; font-size: 26px; }
  .holder-role { font-size: 18px; margin-top: 4px; }
  .contacts {
    position: absolute; right: 30px; top: 260px;
    list-style: none;
    color: var(--white);
    font-size: 17.5px;
  }
  .contacts li {
    display: flex; align-items: center; justify-content: flex-end;
    height: 26.5px;
  }
  .contacts svg { width: 18px; height: 18px; margin-left: 14px; flex: none; }
</style>
</head>
<body>

<section class="card card-front">
  <span class="front-brand">RW Office Partners</span>
</section>

<section class="card card-back">
  <svg class="back-wave" viewBox="0 0 712 418" width="712" height="418">
    <path fill="var(--mauve)" d="M712,40 C560,40 470,110 380,190 C290,270 150,302 0,302 L0,418 L712,418 Z"/>
    <path fill="var(--slate)" d="M712,26 C560,24 460,98 370,178 C280,256 140,288 0,290 L0,302 C150,302 290,270 380,190 C470,110 560,40 712,40 Z"/>
    <path fill="none" stroke="var(--slate)" stroke-width="5" stroke-linecap="round" d="M60,288 C190,282 290,250 352,212"/>
  </svg>

  <span class="back-brand">RW Office Partners</span>
  <p class="tagline">Your organised problem solver</p>

  <div class="holder">
    <p class="holder-name">Marisol Wrenfield</p>
    <p class="holder-role">Virtual Assistant</p>
  </div>

  <ul class="contacts">
    <li>61 482 907 236
      <svg viewBox="0 0 20 20" aria-hidden="true"><path fill="var(--white)" d="M3 7c0-2 3-4 7-4s7 2 7 4v1h-3V6.5C13 6 12 5.5 10 5.5S7 6 6 6.5V8H3zM6 9h8l2 7H4z"/></svg>
    </li>
    <li>@rwofficepartners
      <svg viewBox="0 0 20 20" aria-hidden="true"><rect x="2" y="4" width="16" height="12" fill="var(--white)"/><path d="M2 4l8 7 8-7M2 16l6-6M18 16l-6-6" stroke="var(--mauve)" stroke-width="1.4" fill="none"/></svg>
    </li>
    <li>@rwofficepartners
      <svg viewBox="0 0 20 20" aria-hidden="true"><g fill="none" stroke="var(--white)" stroke-width="1.5"><circle cx="10" cy="10" r="7.5"/><ellipse cx="10" cy="10" rx="3.2" ry="7.5"/><path d="M2.5 10h15M4 6h12M4 14h12"/></g></svg>
    </li>
    <li>www.rwofficepartners.com.au
      <svg viewBox="0 0 20 20" aria-hidden="true"><rect x="2.5" y="2.5" width="15" height="15" rx="2" fill="var(--white)"/></svg>
    </li>
    <li>marisol@rwofficepartners.com.au
      <svg viewBox="0 0 20 20" aria-hidden="true"><circle cx="10" cy="10" r="7.5" fill="none" stroke="var(--white)" stroke-width="2"/></svg>
    </li>
  </ul>
</section>

</body>
</html>
```